Graphic Design Project

Brinley-Cote Publications needs a graphic design for a new product called the "KORV Guide". We develop reference field guides for the construction industry and need the "KORV Guide" design to be worthy of its uniqueness.
The design can be in any color combination but must have a watermark or creative design to go with the name. We are getting ready to head start our 2012 volumes and need a new look.
Please do not add anything that looks like construction. We want a powerful look that is creative in nature with a new twist.
Please do not add Brinley-Cote Publications into the design since we already have a logo. Please stay true to "KORV Guide" and knock our socks off.
You always do.
Reason: I did not receive as many designs as I would have expected. I responded to all designers with feedback but was handicapped with the absence of attendees who had accepted my project. I submitted a written concern to Pixel Harbor a few days ago with no response.
Please help me by increasing my deadline to ensure I receive the design I so critically need to move my business forward successfully.
Thank you.
Graphic Design

```html
<!DOCTYPE html>
<html lang="en">
<head>
<meta charset="utf-8">
<title>KORV Guide – cover colourways</title>
<link rel="stylesheet" href="https://fonts.googleapis.com/css2?family=Crimson+Pro:wght@700&display=swap">
<style>
  :root {
    --page: #ffffff;
    --title-ink: #16167e;
    --guide-ink: #6b5a56;

    --rose-light: #f2dedb;
    --rose-tint: #e8b8b4;
    --rose-deep: #ad5652;
    --slate-light: #e4e4f2;
    --slate-tint: #9aa6b8;
    --slate-deep: #3e3ea0;
    --sage-light: #e2f0e6;
    --sage-tint: #a6c6b2;
    --sage-deep: #23844a;
    --gold-light: #f6eed2;
    --gold-tint: #f8e6a0;
    --gold-deep: #c49a26;
  }
  html, body {
    margin: 0;
    width: 900px;
    height: 1200px;
    overflow: hidden;
    background: var(--page);
  }
  .sheet {
    position: relative;
    width: 900px;
    height: 1200px;
  }
  .cover {
    position: absolute;
    width: 412px;
    height: 580px;
  }
  .cover--rose  { left: 3px;   top: 0; }
  .cover--slate { left: 488px; top: 0; }
  .cover--sage  { left: 3px;   top: 615px; }
  .cover--gold  { left: 488px; top: 615px; }
  .cover svg { display: block; width: 412px; height: 580px; }
  .cover-title {
    font-family: "Crimson Pro", Georgia, serif;
    font-weight: 700;
    font-size: 180px;
    fill: var(--title-ink);
  }
  .cover-subtitle {
    font-family: "Crimson Pro", Georgia, serif;
    font-weight: 700;
    font-size: 54px;
    fill: var(--guide-ink);
  }
</style>
</head>
<body>
<main class="sheet">

  <section class="cover cover--rose">
    <svg viewBox="0 0 412 580" aria-label="KORV Guide cover, rose">
      <defs>
        <linearGradient id="rose-field" x1="0" y1="0" x2="0" y2="1">
          <stop offset="0" style="stop-color:var(--rose-light)"/>
          <stop offset="1" style="stop-color:var(--rose-deep)"/>
        </linearGradient>
        <radialGradient id="rose-glow" cx="0.65" cy="0.35" r="0.6">
          <stop offset="0" stop-color="#fff" stop-opacity="0.9"/>
          <stop offset="1" stop-color="#fff" stop-opacity="0"/>
        </radialGradient>
      </defs>
      <path d="M0 120 Q180 20 412 40 L412 580 L0 580 Z" style="fill:var(--rose-tint)"/>
      <rect x="0" y="120" width="412" height="460" fill="url(#rose-field)"/>
      <ellipse cx="320" cy="250" rx="200" ry="130" fill="url(#rose-glow)"/>
      <path d="M0 255 Q200 300 412 480 L412 580 L300 580 Q180 380 0 300 Z" style="fill:var(--rose-deep)" opacity="0.35"/>
      <g role="img" aria-label="Translucent glass gear ring watermark">
        <circle cx="150" cy="360" r="175" fill="none" stroke="#fff" stroke-width="26" opacity="0.3"/>
      </g>
      <text class="cover-title" x="12" y="126" textLength="388" lengthAdjust="spacingAndGlyphs">KORV</text>
      <text class="cover-subtitle" transform="translate(382 325) rotate(-90)">Guide</text>
    </svg>
  </section>

  <section class="cover cover--slate">
    <svg viewBox="0 0 412 580" aria-label="KORV Guide cover, slate blue">
      <defs>
        <linearGradient id="slate-field" x1="0" y1="0" x2="0" y2="1">
          <stop offset="0" style="stop-color:var(--slate-light)"/>
          <stop offset="1" style="stop-color:var(--slate-deep)"/>
        </linearGradient>
        <radialGradient id="slate-glow" cx="0.65" cy="0.35" r="0.6">
          <stop offset="0" stop-color="#fff" stop-opacity="0.9"/>
          <stop offset="1" stop-color="#fff" stop-opacity="0"/>
        </radialGradient>
      </defs>
      <path d="M0 120 Q180 20 412 40 L412 580 L0 580 Z" style="fill:var(--slate-tint)"/>
      <rect x="0" y="120" width="412" height="460" fill="url(#slate-field)"/>
      <ellipse cx="320" cy="250" rx="200" ry="130" fill="url(#slate-glow)"/>
      <path d="M0 255 Q200 300 412 480 L412 580 L300 580 Q180 380 0 300 Z" style="fill:var(--slate-deep)" opacity="0.35"/>
      <g role="img" aria-label="Translucent glass gear ring watermark">
        <circle cx="150" cy="360" r="175" fill="none" stroke="#fff" stroke-width="26" opacity="0.3"/>
      </g>
      <text class="cover-title" x="12" y="126" textLength="388" lengthAdjust="spacingAndGlyphs">KORV</text>
      <text class="cover-subtitle" transform="translate(382 325) rotate(-90)">Guide</text>
    </svg>
  </section>

  <section class="cover cover--sage">
    <svg viewBox="0 0 412 580" aria-label="KORV Guide cover, sage green">
      <defs>
        <linearGradient id="sage-field" x1="0" y1="0" x2="0" y2="1">
          <stop offset="0" style="stop-color:var(--sage-light)"/>
          <stop offset="1" style="stop-color:var(--sage-deep)"/>
        </linearGradient>
        <radialGradient id="sage-glow" cx="0.65" cy="0.35" r="0.6">
          <stop offset="0" stop-color="#fff" stop-opacity="0.9"/>
          <stop offset="1" stop-color="#fff" stop-opacity="0"/>
        </radialGradient>
      </defs>
      <path d="M0 120 Q180 20 412 40 L412 580 L0 580 Z" style="fill:var(--sage-tint)"/>
      <rect x="0" y="120" width="412" height="460" fill="url(#sage-field)"/>
      <ellipse cx="320" cy="250" rx="200" ry="130" fill="url(#sage-glow)"/>
      <path d="M0 255 Q200 300 412 480 L412 580 L300 580 Q180 380 0 300 Z" style="fill:var(--sage-deep)" opacity="0.35"/>
      <g role="img" aria-label="Translucent glass gear ring watermark">
        <circle cx="150" cy="360" r="175" fill="none" stroke="#fff" stroke-width="26" opacity="0.3"/>
      </g>
      <text class="cover-title" x="12" y="126" textLength="388" lengthAdjust="spacingAndGlyphs">KORV</text>
      <text class="cover-subtitle" transform="translate(382 325) rotate(-90)">Guide</text>
    </svg>
  </section>

  <section class="cover cover--gold">
    <svg viewBox="0 0 412 580" aria-label="KORV Guide cover, gold">
      <defs>
        <linearGradient id="gold-field" x1="0" y1="0" x2="0" y2="1">
          <stop offset="0" style="stop-color:var(--gold-light)"/>
          <stop offset="1" style="stop-color:var(--gold-deep)"/>
        </linearGradient>
        <radialGradient id="gold-glow" cx="0.65" cy="0.35" r="0.6">
          <stop offset="0" stop-color="#fff" stop-opacity="0.9"/>
          <stop offset="1" stop-color="#fff" stop-opacity="0"/>
        </radialGradient>
      </defs>
      <path d="M0 120 Q180 20 412 40 L412 580 L0 580 Z" style="fill:var(--gold-tint)"/>
      <rect x="0" y="120" width="412" height="460" fill="url(#gold-field)"/>
      <ellipse cx="320" cy="250" rx="200" ry="130" fill="url(#gold-glow)"/>
      <path d="M0 255 Q200 300 412 480 L412 580 L300 580 Q180 380 0 300 Z" style="fill:var(--gold-deep)" opacity="0.35"/>
      <g role="img" aria-label="Translucent glass gear ring watermark">
        <circle cx="150" cy="360" r="175" fill="none" stroke="#fff" stroke-width="26" opacity="0.3"/>
      </g>
      <text class="cover-title" x="12" y="126" textLength="388" lengthAdjust="spacingAndGlyphs">KORV</text>
      <text class="cover-subtitle" transform="translate(382 325) rotate(-90)">Guide</text>
    </svg>
  </section>

</main>
</body>
</html>
```